Website Design for Videographer

I am looking to update my website - www.brinolvaske.com. I am a wedding videographer who specialises in natural and documentary videography.

The website will be built by my designer using the Wordpress Plinthworx framework.

Requirements;
I want the website to have a clean white look mixed in with video footage.
Needs to be classy. At the moment my website uses a lot of Gold. On the new look I DO NOT want gold.

Need a web and mobile design for the following 12 pages;

* Home page (need to have example videos and text)
* About (this is about me and my service)
* Videos (examples of my work)
* Testimonials
* Packages
* Contact
* Content (this is to show social media content that I am making in a vertical format and advertise this service).
* Blog (index page for blog)
* Blog pages (individual pages for blog content)
* Wedding Venues Index Page (https://brinolvaske.com/north-east-wedding-venues/)
* Individual venue pages (https://brinolvaske.com/north-east-wedding-venues/marlow-tendle-lodge-wedding-videos/) - Needs to show videos, photos, text as is on the current page.
* Venue Tours (https://brinolvaske.com/wedding-venue-tours/)

My current logo is attached however on the website I want to go for a black and white style for it.

Example styles I like however must not be copied.
https://joswelbrant.co.uk/about/
https://oakandripple.co.uk/ (if done in white)
https://tumblemothpictures.co.uk/

Target Market(s)

Couples getting married aged 25-35

Industry/Entity Type

Weddings

Number of Pages Required

5+ page

Font styles to use
Sans Serif

Requirements
Must have
• A classy look, black and white, use videos and photos.
Should not have
• Gold colour

```html
<!DOCTYPE html>
<html lang="en">
<head>
<meta charset="utf-8">
<title>Brin Olvaske Wedding Films – North East Wedding Videographer</title>
<link rel="stylesheet" href="https://fonts.googleapis.com/css2?family=Plus+Jakarta+Sans:wght@400;500;600;700;800&display=swap">
<style>
:root{
  --ink:#0b0b0b;
  --paper:#ffffff;
  --mist:#f3f3f3;
  --muted:#6b6b6b;
  --line:#d9d9d9;
  --stone-1:#cfc8bd;
  --stone-2:#7d766c;
  --clay-1:#c79d78;
  --clay-2:#6e5440;
  --grass:#6f8a4e;
  --sky:#dfe3e6;
  --graphite-1:#2a2a2a;
  --graphite-2:#8a8a8a;
}
*{margin:0;padding:0;box-sizing:border-box}
html,body{width:1200px;height:4839px;overflow:hidden}
body{position:relative;background:var(--paper);color:var(--ink);font-family:"Plus Jakarta Sans",Arial,sans-serif}
.abs{position:absolute}
.media{position:absolute;overflow:hidden}
.play{position:absolute;width:64px;height:64px;margin:-32px 0 0 -32px}
.link{position:absolute;font-size:12px;font-weight:700;display:flex;align-items:center;gap:10px;white-space:nowrap}
.link svg{width:8px;height:10px}
.body-copy{position:absolute;font-size:12.5px;line-height:20px;color:var(--muted)}

/* top bar & header */
.award-bar{left:0;top:0;width:1200px;height:32px;font-size:12px;display:flex;align-items:center;justify-content:center}
.site-header{left:0;top:32px;width:1200px;height:180px;background:var(--ink);color:var(--paper)}
.brand{position:absolute;left:0;width:100%;top:32px;display:flex;flex-direction:column;align-items:center;gap:10px}
.brand-mark{width:16px;height:16px;background:var(--paper)}
.brand-name{font-size:12px;font-weight:600;letter-spacing:3px}
.main-nav{position:absolute;top:131px;left:0;width:100%;font-size:12.5px}
.main-nav span{display:flex;align-items:center;gap:8px}

/* hero */
.hero{left:0;top:212px;width:1200px;height:400px;background:linear-gradient(90deg,var(--stone-1) 0%,var(--stone-2) 22%,var(--sky) 38%,#3d3a36 56%,var(--stone-2) 72%,var(--sky) 86%,#9aa0a1 100%)}
.intro-title{left:62px;top:646px;font-size:56px;line-height:60px;font-weight:700;letter-spacing:-.5px}
.intro-copy{left:763px;top:642px;width:380px}

/* packages */
.tabs{left:0;top:874px;width:1200px;font-size:12px;font-weight:600}
.tab{position:absolute;top:0;color:var(--muted)}
.tab.active{color:var(--ink)}
.tab-line{left:662px;top:903px;width:92px;height:2px;background:var(--ink)}
.package-media{left:60px;top:925px;width:1077px;height:602px;background:linear-gradient(90deg,#b9b3ab 0%,#8c867e 30%,#d8d2c8 48%,#6d6a63 62%,#a7a097 80%,#7f8a5d 100%)}
.package-shade{left:60px;top:925px;width:560px;height:602px;background:linear-gradient(90deg,rgba(0,0,0,.45),rgba(0,0,0,0))}
.package-title{left:107px;top:1306px;font-size:34px;font-weight:700;color:var(--paper)}
.package-copy{left:107px;top:1360px;width:420px;color:#f2f2f2;font-size:12.5px;line-height:20px}

/* feature rows */
.feature-title{font-size:33px;line-height:43px;font-weight:700}

/* wedding films */
.films{left:0;top:2430px;width:1200px;height:732px;background:var(--mist)}
.films-title{left:0;top:2460px;width:1200px;text-align:center;font-size:32px;font-weight:700}
.films-media{left:60px;top:2526px;width:1077px;height:549px;background:linear-gradient(120deg,#d8b594 0%,var(--clay-1) 35%,#5c4638 55%,var(--clay-1) 75%,#b98f6d 100%)}
.nav-dot{position:absolute;width:34px;height:34px;border-radius:50%;display:flex;align-items:center;justify-content:center}
.dots{left:0;top:3040px;width:1200px;display:flex;justify-content:center;gap:14px}
.dots i{width:9px;height:9px;border-radius:50%;background:rgba(255,255,255,.55)}
.dots i:first-child{background:var(--paper)}

/* stories */
.story-title{left:60px;top:3216px;font-size:33px;line-height:43px;font-weight:700}
.story-copy{left:638px;top:3222px;width:499px;text-align:right}
.story-card{position:absolute;top:3371px;height:385px}

/* award */
.award-media{left:598px;top:3840px;width:469px;height:384px;background:linear-gradient(135deg,var(--graphite-1) 0%,#4a4a4a 40%,var(--graphite-2) 75%,#bdbdbd 100%)}

/* cta */
.cta{left:60px;top:4309px;width:1077px;height:163px;background:linear-gradient(90deg,#3a2f2a,#6b5a4f 35%,#2b2522 60%,#5a4a40 100%)}
.cta-title{left:0;top:4354px;width:1200px;text-align:center;font-size:30px;font-weight:700;color:var(--paper)}

/* footer */
.site-footer{left:0;top:4534px;width:1200px;height:305px;background:var(--ink);color:var(--paper);border-radius:20px 20px 0 0}
.foot-head{position:absolute;font-size:12.5px;font-weight:700;white-space:nowrap}
.foot-item{position:absolute;font-size:12px;color:#d6d6d6;white-space:nowrap}
.social{position:absolute;display:flex;flex-direction:column;gap:8px;font-size:11.5px;color:#d6d6d6}
.social span{display:flex;align-items:center;gap:7px;white-space:nowrap}
.social i{width:10px;height:10px;border-radius:50%;background:var(--paper)}
</style>
</head>
<body>

<svg width="0" height="0" class="abs"><defs>
  <symbol id="chev" viewBox="0 0 8 10"><path d="M2 1l4 4-4 4" fill="none" stroke="currentColor" stroke-width="1.6"/></symbol>
  <symbol id="play" viewBox="0 0 64 64"><circle cx="32" cy="32" r="29" fill="none" stroke="#fff" stroke-width="3"/><path d="M26 20v24l19-12z" fill="#fff"/></symbol>
</defs></svg>

<div class="abs award-bar">Vowline Wedding Awards 2024 - Wedding Videography Winner</div>

<header class="abs site-header">
  <div class="brand"><span class="brand-mark"></span><span class="brand-name">BRIN OLVASKE</span></div>
  <nav class="main-nav">
    <span style="position:absolute;left:265px">About</span>
    <span style="position:absolute;left:358px">Packages <svg width="9" height="6" viewBox="0 0 9 6"><path d="M1 1l3.5 3.5L8 1" fill="none" stroke="#fff" stroke-width="1.5"/></svg></span>
    <span style="position:absolute;left:497px">Wedding Films <svg width="9" height="6" viewBox="0 0 9 6"><path d="M1 1l3.5 3.5L8 1" fill="none" stroke="#fff" stroke-width="1.5"/></svg></span>
    <span style="position:absolute;left:669px">Testimonials</span>
    <span style="position:absolute;left:802px">Blog</span>
    <span style="position:absolute;left:886px">Enquire</span>
  </nav>
</header>

<div class="media hero" role="img" aria-label="Wedding film still: bride and groom walking between tall stone columns"></div>
<svg class="play" style="left:600px;top:412px"><use href="#play"/></svg>

<h1 class="abs intro-title">North East Wedding<br>Videographer</h1>
<p class="body-copy intro-copy">A North East Wedding Videographer with timeless, heartfelt films that preserve every beautiful moment and emotion of your wedding. Let me tell your unique love story through a lens, so you can relive it for years to come</p>
<span class="link" style="left:763px;top:754px">Make Enquire <svg><use href="#chev"/></svg></span>

<div class="abs tabs">
  <span class="tab" style="left:459px">Signature</span>
  <span class="tab" style="left:586px">Gold</span>
  <span class="tab active" style="left:680px">Platinum</span>
</div>
<div class="abs tab-line"></div>

<div class="media package-media" role="img" aria-label="Platinum package film still: couple holding hands beside stone columns on a lawn"></div>
<div class="abs package-shade"></div>
<svg class="play" style="left:600px;top:1226px"><use href="#play"/></svg>
<h2 class="abs package-title">Platinum Package</h2>
<p class="abs package-copy">Everything in the gold package (highlights, ceremony, speeches, long video and teaser) plus any even longer feature film featuring more moments from your wedding day. You will receive at least 100 screen images, perfect for sharing on social media.</p>
<span class="link" style="left:107px;top:1471px;color:#fff">Learn More <svg><use href="#chev"/></svg></span>

<h2 class="abs feature-title" style="left:69px;top:1630px">Stunning North East Wedding<br>Films</h2>
<p class="body-copy" style="left:69px;top:1748px;width:498px">A trusted and acclaimed North East wedding videographer who has more than 25 years of videography experience. From beautiful barns and luxurious country hotels to sun-drenched Greek Islands and ancient Italian abbeys, he has filmed all kinds of unforgettable weddings. If you're looking for a highly experienced wedding videographer who focuses on your story, the "goosebump" moments and the emotions filling the room as you entertain your guests, then get in touch with Brin today.</p>
<span class="link" style="left:69px;top:1934px">Watch Movie <svg><use href="#chev"/></svg></span>
<div class="media" style="left:606px;top:1607px;width:515px;height:366px;background:linear-gradient(180deg,var(--sky) 0%,#a99d92 35%,#8b6f60 60%,#8d8983 100%)" role="img" aria-label="Couple embracing in front of a historic brick gatehouse"></div>

<div class="media" style="left:75px;top:2014px;width:518px;height:345px;background:linear-gradient(90deg,#e6e6e4 0%,#3a3836 20%,#e9e9e7 45%,#cfcac4 65%,#3e3b38 80%,#e4e4e2 100%)" role="img" aria-label="Couple embracing beneath a steel bridge structure"></div>
<h2 class="abs feature-title" style="left:628px;top:2036px">Wedding Videography For<br>Natural Moments</h2>
<p class="body-copy" style="left:628px;top:2154px;width:500px">My approach to wedding videography is straightforward: I let you and your guests enjoy the pleasure, love, and festivities of the day. The focus will be on capturing the spontaneous, real interactions that make your wedding so unique. When you look back on your wedding day, I want you to remember the genuine smiles, genuine laughing, and spontaneous moments of emotion that you might have missed in the flurry of events.</p>
<span class="link" style="left:628px;top:2318px">Watch Movie <svg><use href="#chev"/></svg></span>

<section class="abs films"></section>
<h2 class="abs films-title">Wedding Films</h2>
<div class="media films-media" role="img" aria-label="Wedding film still: couple sharing a kiss against a sunlit stone wall"></div>
<svg class="play" style="left:600px;top:2802px"><use href="#play"/></svg>
<span class="nav-dot" style="left:96px;top:2785px;background:rgba(255,255,255,.35);color:#fff"><svg width="8" height="10" style="transform:scaleX(-1)"><use href="#chev"/></svg></span>
<span class="nav-dot" style="left:1067px;top:2785px;background:#fff;color:var(--ink)"><svg width="8" height="10"><use href="#chev"/></svg></span>
<div class="abs dots"><i></i><i></i><i></i><i></i><i></i><i></i></div>
<span class="link" style="left:960px;top:3104px">View All Wedding Films <svg><use href="#chev"/></svg></span>

<h2 class="abs story-title">Every Wedding Has a Story<br>Relive Your Moments for a<br>Lifetime</h2>
<p class="body-copy story-copy">Don't risk forgetting the sounds as well as the sights. The giggles, the vows, the jokes, the speeches, and the music add atmosphere to your wedding video and bring your day back to life each and every time you watch it</p>
<span class="nav-dot" style="left:1060px;top:3298px;background:#8c8c8c;color:#fff"><svg width="8" height="10" style="transform:scaleX(-1)"><use href="#chev"/></svg></span>
<span class="nav-dot" style="left:1103px;top:3298px;background:var(--ink);color:#fff"><svg width="8" height="10"><use href="#chev"/></svg></span>

<div class="media story-card" style="left:60px;width:352px;background:linear-gradient(180deg,#d9d2c8,#a89a8c 60%,#7a5a50)" role="img" aria-label="Bride on a grand staircase in a historic hall"></div>
<div class="abs" style="left:60px;top:3530px;width:352px;text-align:center;color:#fff">
  <div style="font-size:32px;font-weight:700">Maren's Wedding</div>
  <div style="font-size:11.5px;font-weight:700;margin-top:6px">Watch Full Story &rsaquo;</div>
</div>
<div class="media story-card" style="left:423px;width:352px;background:linear-gradient(180deg,#5d7545 0%,#a5b39a 45%,var(--grass) 75%,#55703a 100%)" role="img" aria-label="Couple walking hand in hand on a lawn"></div>
<div class="media story-card" style="left:786px;width:351px;background:linear-gradient(90deg,#4a3325 0%,#6b4b36 35%,#d9cfc3 60%,#b8a794 100%)" role="img" aria-label="Bride holding a bouquet beside a timber door"></div>
<div class="media story-card" style="left:1148px;width:52px;background:linear-gradient(180deg,#cfd4d6,#8d8f8c)" role="img" aria-label="Couple outside a historic building"></div>

<h2 class="abs feature-title" style="left:129px;top:3854px">Vowline Wedding Awards<br>2024 Winner</h2>
<p class="body-copy" style="left:129px;top:3968px;width:440px">I'm honoured to have been the only wedding videographer from the North East to win the Vowline Wedding Awards 2024. This award represents more to me than a simple pat on the back; it's evidence of the incredible moments I've recorded for couples on their wedding day. The fact that this victory is entirely the result of the votes and encouraging remarks from the couples I've had the honour of working with makes it even more noteworthy. What really sealed the deal for me on this award was their satisfaction and the memories we've made together.</p>
<span class="link" style="left:129px;top:4195px">Read More <svg><use href="#chev"/></svg></span>
<div class="media award-media" role="img" aria-label="Award winner artwork for the 2024 wedding awards"></div>

<div class="media cta" role="img" aria-label="Close-up of wedding details on a dark wooden surface"></div>
<h2 class="abs cta-title">Want An Amazing Wedding Video?</h2>
<span class="link" style="left:543px;top:4411px;color:#fff">Make Enquiry <svg><use href="#chev"/></svg></span>

<footer class="abs site-footer">
  <div class="abs" style="left:51px;top:26px;display:flex;flex-direction:column;align-items:flex-start;gap:9px">
    <span class="brand-mark"></span><span class="brand-name">BRIN OLVASKE</span>
  </div>
  <p class="abs" style="left:51px;top:105px;width:410px;font-size:12px;line-height:18.5px;color:#d6d6d6">Brin Olvaske - I am a wedding videographer who specialises in natural and documentary videography. A North East Wedding Videographer with timeless, heartfelt films that preserve every beautiful moment and emotion of your wedding. Let me tell your unique love story through a lens, so you can relive it for years to come</p>

  <span class="foot-head" style="left:591px;top:28px">Packages</span>
  <span class="foot-item" style="left:591px;top:92px">Signature</span>
  <span class="foot-item" style="left:591px;top:133px">Gold</span>
  <span class="foot-item" style="left:591px;top:173px">Platinum</span>

  <span class="foot-head" style="left:784px;top:28px">Links</span>
  <span class="foot-item" style="left:784px;top:92px">FAQ's</span>
  <span class="foot-item" style="left:784px;top:128px">Blog</span>
  <span class="foot-item" style="left:784px;top:163px">Commercial Videography</span>
  <span class="foot-item" style="left:784px;top:198px">Lake District Video</span>

  <span class="foot-head" style="left:1059px;top:28px">Social Media</span>
  <div class="social" style="left:1059px;top:56px"><span><i></i>Circlepage</span><span><i></i>Postline</span></div>

  <div class="abs" style="left:51px;top:244px;width:1098px;height:1px;background:#3a3a3a"></div>
  <p class="abs" style="left:0;top:264px;width:1200px;text-align:center;font-size:12px;color:#d6d6d6">© 2024 Brin Olvaske Wedding Film Limited. All Rights Reserved.</p>
</footer>

</body>
</html>
```